Internal Office Slogans / Motto / Vision Statements

Hi. We would like to put up some posters around the office with quotations such as -
-”Do what you do so well that they will want to see it again and bring their friends.”- Hollis Brandt
-Make your customers feel heard and understood. Make your customers feel respected and liked. Make your customers feel appreciated and helped. Understand that you can do none of these things unless you are sincere about them.
Terrence Oakley
- It’s a very predictable and satisfying phenomenon: whenever we get better, our customers do too.
Cal Pruett
-Catch people in the act of performing extraordinary customer service. Treat them like heroes. Tell their stories, far and wide.
Ned Farraday

The purpose of the posters is to reiterate our culture and vision within the organisation. They should be clean, crisp and eye catching, not gaudy or bright. Professional, bold and strong.

The company website and logo is at http://www.nexoraweb.com.au
Print size will be A1

Thanks for participating & looking forward to seeing your great work.
Updates

Hi All. . 

So to reiterate we are looking for one background design to be used for multiple quotes...  The list of quotes are as follows: 

Support and or Sales Office

 

Make your customers feel heard and understood.Make your customers feel respected and liked. Make your customers feelappreciated and helped. Understand that you can do none of these things unlessyou are sincere about them.

Terrence Oakley

 

Nothing liberates our greatness like the desireto help, the desire to serve

Dorothea Quill

 

It’s a very predictable and satisfying phenomenon:whenever we get better, our customers do too.

Cal Pruett

 

Success means we go to sleep at night knowingthat our talents and abilities were used in a way that served others.

Dorothea Quill.

 

The sole purpose of business is to create, serveand satisfy a customer, from beginning to end – and that’s everyone’s job.

Ned Farraday

 

We don’t celebrate closing a sale, we celebrateopening a relationship.

Rosalind Hext

I will never make you a promise – unless I giveyou a plan and procedure to make that promise possible.

Bo Tennant

 

Customers feel we take them for granted; onlyshow interest when we want an order; lavish our time on prospects; communicatemainly by invoice; are fixated on big accounts; drop them like hot potatoesonce we have the order; don’t follow through on promises; and satisfy our ownbureaucracy rather than their needs. We can do better than that, much better.

Alan P Merrow.

 

 

General and public area

 

Catch people in the act of performingextraordinary customer service. Treat them like heroes. Tell their stories, farand wide.

Ned Farraday

 

 

We see our customers as invited guests to aparty, and we are the hosts. It’s our job every day to make every importantaspect of the customer experience a little bit better." Carl Voight - Founder andCEO of Halverin

 

"If you do build a great experience,customers tell each other about that. Word of mouth is verypowerful."  Carl Voight

 

It's not a faithin technology. It's faith in people. Rick Palmer

 

“Being the richest man in the cemetery doesn’tmatter to me … Going to bed at night saying we’ve done something wonderful…that’s what matters to me.” Rick Palmer

 

The customer experience is the next competitivebattleground. Lance Morrow, CIO, Vantor Computers

 

”Do what you do so well that they will want tosee it again and bring their friends.”- Hollis Brandt

In the world of internet customer service, it isimportant to remember your competitor is only a mouse click away. FrankHolden (not sure who he is but like the quote).

The customer is why you go to work. If they goaway, you do, too. Peter Lindqvist (?)

 

MaybeSome for Sales or Build Team:

Quality is remembered long after the price is forgotten. Marzetti Family Slogan

```html
<!DOCTYPE html>
<html lang="en">
<head>
<meta charset="utf-8">
<title>Catch People in the Act – Office Poster</title>
<link rel="stylesheet" href="https://fonts.googleapis.com/css2?family=Josefin+Sans:wght@300;400;600;700&display=swap">
<style>
  :root {
    --bg-light: #fcf5e2;
    --bg-warm: #f7d3ae;
    --ink: #2f2f2f;
    --ink-soft: #3a3a3a;
    --violet: #5b5aa6;
    --brick: #a0302f;
    --teal: #5b9a86;
    --mauve: #a57ea9;
    --peach: #e2a679;
    --leaf: #6a9a3c;
  }
  html, body {
    margin: 0;
    padding: 0;
    overflow: hidden;
  }
  .poster {
    position: relative;
    width: 849px;
    height: 1200px;
    overflow: hidden;
    background: linear-gradient(160deg, var(--bg-light) 0%, var(--bg-light) 35%, var(--bg-warm) 100%);
    font-family: "Josefin Sans", sans-serif;
    color: var(--ink);
  }
  .quote-line {
    position: absolute;
    left: 0;
    width: 100%;
    margin: 0;
    text-align: center;
    text-transform: uppercase;
    line-height: 1;
    white-space: nowrap;
  }
  .light { font-weight: 300; letter-spacing: 0.04em; }
  .bold { font-weight: 700; letter-spacing: 0.02em; }

  .line-catch    { top: 33px;  font-size: 52px; }
  .line-act      { top: 106px; font-size: 52px; }
  .line-perform  { top: 174px; font-size: 52px; }
  .line-extra    { top: 241px; font-size: 59px; color: var(--teal); }
  .line-customer { top: 309px; font-size: 79px; color: var(--ink); }
  .line-service  { top: 390px; font-size: 106px; color: var(--mauve); }
  .line-treat    { top: 494px; font-size: 52px; }
  .line-heroes   { top: 551px; font-size: 106px; color: var(--peach); }
  .line-stories  { top: 649px; font-size: 55px; }
  .line-wide     { top: 717px; font-size: 47px; color: var(--leaf); }

  .accent-violet { color: var(--violet); font-weight: 400; }
  .accent-brick  { color: var(--brick); font-weight: 700; }
  .accent-strong { font-weight: 600; }

  .divider {
    position: absolute;
    top: 950px;
    left: 28px;
    width: 793px;
    height: 8px;
  }
  .attribution {
    position: absolute;
    top: 1003px;
    left: 62px;
    margin: 0;
    font-size: 52px;
    font-weight: 300;
    letter-spacing: 0.03em;
    text-transform: uppercase;
    line-height: 1;
    color: var(--ink-soft);
  }
</style>
</head>
<body>
  <main class="poster">
    <p class="quote-line light line-catch"><span class="accent-violet">Catch</span> people</p>
    <p class="quote-line light line-act">In the <span class="accent-brick">act</span> of</p>
    <p class="quote-line light line-perform">Performing</p>
    <p class="quote-line bold line-extra">Extraordinary</p>
    <p class="quote-line bold line-customer">Customer</p>
    <p class="quote-line bold line-service">Service.</p>
    <p class="quote-line light line-treat">Treat them like</p>
    <p class="quote-line bold line-heroes">Heroes.</p>
    <p class="quote-line light line-stories">Tell their <span class="accent-strong">stories.</span></p>
    <p class="quote-line bold line-wide">Far and wide.</p>

    <svg class="divider" viewBox="0 0 793 8" aria-hidden="true">
      <line x1="0" y1="4" x2="793" y2="4" stroke="#2f2f2f" stroke-width="4" stroke-dasharray="4 4"/>
    </svg>

    <p class="attribution">-Ned Farraday</p>
  </main>
</body>
</html>
```